I need a SEO-friendly Wordpress website (making sure to style H1, H2, H3, etc correctly) for a Hawaii-based law firm called Meridian Crest Legal Group. Comparable websites include https://brvlaw.example/ and https://www.lomrit.example/ for design reference. The current copy on the TarnAdvocate.example website can be used.

```html
<!DOCTYPE html>
<html lang="en">
<head>
<meta charset="utf-8">
<title>Meridian Crest Legal Group</title>
<link rel="stylesheet" href="https://fonts.googleapis.com/css2?family=Noto+Serif:wght@400;700&family=Lato:ital,wght@0,400;0,700;1,400&display=swap">
<style>
:root{
  --navy:#1f3a5f;
  --navy-dark:#1a3250;
  --green:#5f8a0f;
  --text:#555b63;
  --light:#f3f4f6;
  --white:#ffffff;
  --ghost:#e9ebef;
  --map:#eceee9;
}
*{margin:0;padding:0;box-sizing:border-box}
html,body{width:1200px;height:2690px;overflow:hidden;background:var(--white)}
body{font-family:"Lato",sans-serif;color:var(--text);position:relative}
.abs{position:absolute}
.btn{position:absolute;background:var(--green);color:var(--white);font:700 14px "Lato",sans-serif;text-transform:uppercase;display:flex;align-items:center;justify-content:center;gap:8px;width:150px;height:30px;text-decoration:none}
.btn svg{width:13px;height:13px}

/* header */
.site-header{position:absolute;left:0;top:0;width:1200px;height:107px;border-top:3px solid var(--green);background:var(--white)}
.brand{left:143px;top:31px;font:700 25px "Noto Serif",serif;color:var(--navy);letter-spacing:.2px}
.tagline{left:143px;top:72px;font-size:12px;color:#666}
.call-icon{left:650px;top:11px;width:40px;height:40px}
.call-label{left:698px;top:13px;font-size:13px;color:#777}
.call-number{left:698px;top:29px;font:700 21px "Lato",sans-serif;color:var(--navy)}
.search{left:857px;top:15px;width:200px;height:34px;border:1px solid #d4d7dc;display:flex}
.search span{flex:1;padding:8px 12px;font-size:13px;color:#888}
.search b{width:42px;background:var(--navy);display:flex;align-items:center;justify-content:center}
.main-nav{right:143px;top:75px;display:flex;gap:25px;font-size:15px;color:#222}

/* hero */
.hero{left:0;top:107px;width:1200px;height:510px;background:linear-gradient(100deg,#3a3330 0%,#5a5550 40%,#8c8a88 70%,#b9b6b2 100%)}
.hero-panel{left:143px;top:243px;width:520px;height:240px}
.hero-title{left:195px;top:262px;font:700 43px/50px "Noto Serif",serif;color:var(--white)}
.hero-text{left:201px;top:371px;font-size:14px;line-height:20px;color:#e8ecf2}
.arrow-circle{width:42px;height:42px;border-radius:50%;display:flex;align-items:center;justify-content:center}

/* news */
.news{left:0;top:617px;width:1200px;height:45px;background:var(--light)}
.news-label{left:97px;top:624px;font:700 25px "Noto Serif",serif;color:var(--white)}
.news-text{left:340px;top:631px;font-size:14px;color:#333}

/* about */
.about-photo{left:166px;top:727px;width:368px;height:368px;border-radius:50%;background:linear-gradient(160deg,#dfe3e6,#8a939c 60%,#2b3440)}
.about-h2{left:586px;top:740px;font:700 40px "Noto Serif",serif;color:var(--navy)}
.about-h3{left:586px;top:792px;font:400 25px "Noto Serif",serif;color:var(--green)}
.about-copy{left:586px;top:840px;width:470px;font-size:14px;line-height:21.6px;color:#555}
.about-copy p+p{margin-top:21px}
.ghost-word{font:700 90px "Noto Serif",serif;color:var(--ghost);white-space:nowrap}

/* practice */
.practice{left:0;top:1128px;width:1200px;height:730px;background:linear-gradient(180deg,#f1f2f4,#e9eaee 60%,#f4f5f7)}
.section-h2{width:1200px;left:0;text-align:center;font:700 40px "Noto Serif",serif;color:var(--navy)}
.card{position:absolute;top:1359px;width:287px;height:347px;background:var(--white);box-shadow:0 2px 6px rgba(0,0,0,.12)}
.card-img{width:287px;height:192px;position:relative}
.card-tag{position:absolute;right:0;bottom:0;height:40px;width:168px;background:rgba(31,58,95,.92);color:var(--white);font:700 16px "Lato",sans-serif;display:flex;align-items:center;justify-content:center;text-transform:uppercase}
.card p{margin:22px 22px 0 23px;font-size:13px;line-height:21.6px;color:#666}
.card .btn{left:23px;top:294px}

/* testimonials */
.quote{left:0;width:1200px;text-align:center;font-style:italic;font-size:14.5px;line-height:30px;color:#555;top:2008px}
.cite{left:0;width:1200px;text-align:center;top:2113px}
.cite strong{font:700 20px "Lato",sans-serif;color:var(--green)}
.cite em{font-size:14px;color:#333}

/* map */
.map{left:0;top:2206px;width:1200px;height:425px;background:var(--map)}
.contact-card{left:143px;top:2305px;width:329px;height:227px;background:var(--white);box-shadow:0 2px 8px rgba(0,0,0,.1)}
.c-row{position:absolute;left:29px;display:flex;align-items:center;gap:10px;font-size:14px;line-height:21px;color:#444}
.c-icon{width:46px;height:46px;border-radius:50%;display:flex;align-items:center;justify-content:center;flex:none}

/* footer */
.site-footer{left:0;top:2631px;width:1200px;height:59px;background:var(--navy-dark);color:var(--white);font-size:13px}
.site-footer .copy{position:absolute;left:143px;top:21px}
.site-footer nav{position:absolute;right:143px;top:21px;display:flex;gap:8px}
</style>
</head>
<body>

<header class="site-header">
  <div class="abs brand">MERIDIAN CREST LEGAL GROUP</div>
  <div class="abs tagline">DIVORCE AND PERSONAL INJURY LAWYERS</div>
  <svg class="abs call-icon" viewBox="0 0 40 40"><circle cx="20" cy="20" r="18" fill="none" stroke="#5f8a0f" stroke-width="3"/><path d="M13 11c2-1 3 0 4 3 .6 2-1 2.5-1 3.5s3 5 5 5.5c1 .2 1.5-1.5 3-1 3 1 4 2 3 4-1 2-3 3-6 1.5-4-2-8-7-9-11-.5-3 0-4.5 1-5.5z" fill="#5f8a0f"/></svg>
  <div class="abs call-label">Call us :</div>
  <div class="abs call-number">1.808.555.0147</div>
  <div class="abs search"><span>Search...</span><b><svg width="14" height="14" viewBox="0 0 14 14"><circle cx="6" cy="6" r="4" fill="none" stroke="#fff" stroke-width="2"/><path d="M9 9l3.5 3.5" stroke="#fff" stroke-width="2"/></svg></b></div>
  <nav class="abs main-nav"><span>HOME</span><span>PRACTICE AREAS</span><span>ATTORNEYS</span><span>BLOG</span><span>CONTACT US</span></nav>
</header>

<section>
  <div class="abs hero" role="img" aria-label="Photo of smiling attorneys in business suits in a bright office"></div>
  <svg class="abs hero-panel" viewBox="0 0 520 240"><polygon points="0,0 436,0 520,240 0,240" fill="rgba(31,58,95,.93)"/></svg>
  <h1 class="abs hero-title">MERIDIAN CREST<br>LEGAL GROUP</h1>
  <p class="abs hero-text">Lorem ipsum dolor sit amet consectetur adipiscing elit<br>sed do eiusmod tempor incididunt</p>
  <a class="btn" style="left:197px;top:426px">Get Started <svg viewBox="0 0 14 14"><circle cx="7" cy="7" r="7" fill="#fff"/><path d="M5.5 4l3 3-3 3" stroke="#5f8a0f" stroke-width="2" fill="none"/></svg></a>
  <div class="abs arrow-circle" style="left:62px;top:342px;border:1.5px solid #ddd;background:rgba(0,0,0,.25)"><svg width="12" height="16" viewBox="0 0 12 16"><path d="M9 2L3 8l6 6" stroke="#fff" stroke-width="2" fill="none"/></svg></div>
  <div class="abs arrow-circle" style="left:1096px;top:342px;border:1.5px solid #ddd;background:rgba(0,0,0,.25)"><svg width="12" height="16" viewBox="0 0 12 16"><path d="M3 2l6 6-6 6" stroke="#fff" stroke-width="2" fill="none"/></svg></div>
</section>

<section>
  <div class="abs news"></div>
  <svg class="abs" style="left:0;top:617px" width="313" height="45" viewBox="0 0 313 45"><polygon points="0,0 290,0 313,22.5 290,45 0,45" fill="#5f8a0f"/></svg>
  <h3 class="abs news-label">LATEST NEWS</h3>
  <p class="abs news-text">Lorem ipsum dolor sit amet, consectetur adipisc sed do eiusmod tempor incididunt ut labore et dolorna aliqua.</p>
</section>

<section>
  <div class="abs ghost-word" style="left:1070px;top:1080px;transform:rotate(-90deg);transform-origin:0 0;font-size:98px">ABOUT</div>
  <svg class="abs" style="left:148px;top:713px" width="394" height="394" viewBox="0 0 394 394"><circle cx="197" cy="197" r="193" fill="none" stroke="#1f3a5f" stroke-width="5" stroke-dasharray="1030 183" transform="rotate(10 197 197)"/></svg>
  <div class="abs about-photo" role="img" aria-label="Photo of a team of five lawyers standing with arms crossed"></div>
  <h2 class="abs about-h2">ABOUT THE</h2>
  <h3 class="abs about-h3">KONA LAWYERS OF MCLG</h3>
  <div class="abs about-copy">
    <p>Lawyers Serving the Big Island and Neighboring Islands<br>The experienced attorneys in the Meridian Crest Legal Group's Kailua Kona, Hawaii office provide clients with a wide range of litigation expertise, including legal claims involving divorce &amp; family, personal injury, toxic exposures, intellectual property, and real estate.</p>
    <p>Our Kona office also offers commercial and hospitality litigation expertise on behalf of a wide variety of clients, including restaurants,</p>
  </div>
  <a class="btn" style="left:586px;top:1040px">Read More <svg viewBox="0 0 14 14"><circle cx="7" cy="7" r="7" fill="#fff"/><path d="M5.5 4l3 3-3 3" stroke="#5f8a0f" stroke-width="2" fill="none"/></svg></a>
</section>

<section>
  <div class="abs practice" role="img" aria-label="Faint background photo of business people"></div>
  <svg class="abs" style="left:0;top:1127px" width="1200" height="70" viewBox="0 0 1200 70"><path d="M0 0 H1200 V1 Q600 128 0 1 Z" fill="#fff"/></svg>
  <svg class="abs" style="left:0;top:1790px" width="1200" height="70" viewBox="0 0 1200 70"><path d="M0 70 V68 Q600 -40 1200 68 V70Z" fill="#fff"/></svg>
  <div class="abs ghost-word" style="left:28px;top:1425px;transform:rotate(-90deg);transform-origin:0 0;font-size:95px;color:#dfe1e5">AREA</div>
  <h2 class="abs section-h2" style="top:1270px">AREAS OF PRACTICE</h2>

  <article class="card" style="left:143px">
    <div class="card-img" role="img" aria-label="Photo of a stressed couple at a table with documents" style="background:linear-gradient(135deg,#3d3a38,#a9a39c 60%,#e2dfda)"><div class="card-tag">Family &amp; Divorce</div></div>
    <p>Lorem ipsum dolor sit amet, consectetur adipiscing elit, sed do eiusmod tempor enim ad minimamco laboris nisi</p>
    <a class="btn">Read More <svg viewBox="0 0 14 14"><circle cx="7" cy="7" r="7" fill="#fff"/><path d="M5.5 4l3 3-3 3" stroke="#5f8a0f" stroke-width="2" fill="none"/></svg></a>
  </article>
  <article class="card" style="left:456px">
    <div class="card-img" role="img" aria-label="Photo of an injured man in a sling comforted by a woman" style="background:linear-gradient(135deg,#e6e7ea,#9aa8bd 55%,#5b6e8c)"><div class="card-tag">Personal Injury</div></div>
    <p>Lorem ipsum dolor sit amet, consectetur adipiscing elit, sed do eiusmod tempor enim ad minimamco laboris nisi</p>
    <a class="btn">Read More <svg viewBox="0 0 14 14"><circle cx="7" cy="7" r="7" fill="#fff"/><path d="M5.5 4l3 3-3 3" stroke="#5f8a0f" stroke-width="2" fill="none"/></svg></a>
  </article>
  <article class="card" style="left:769px">
    <div class="card-img" role="img" aria-label="Photo of new townhouses under an evening sky" style="background:linear-gradient(180deg,#5e86b8,#d9b99a 45%,#4a4c4f 70%,#2f3133)"><div class="card-tag">Real Estate</div></div>
    <p>Lorem ipsum dolor sit amet, consectetur adipiscing elit, sed do eiusmod tempor enim ad minimamco laboris nisi</p>
    <a class="btn">Read More <svg viewBox="0 0 14 14"><circle cx="7" cy="7" r="7" fill="#fff"/><path d="M5.5 4l3 3-3 3" stroke="#5f8a0f" stroke-width="2" fill="none"/></svg></a>
  </article>
  <div class="abs arrow-circle" style="left:63px;top:1512px;background:#6f7378"><svg width="12" height="16" viewBox="0 0 12 16"><path d="M9 2L3 8l6 6" stroke="#fff" stroke-width="2" fill="none"/></svg></div>
  <div class="abs arrow-circle" style="left:1096px;top:1512px;background:#6f7378"><svg width="12" height="16" viewBox="0 0 12 16"><path d="M3 2l6 6-6 6" stroke="#fff" stroke-width="2" fill="none"/></svg></div>
</section>

<section>
  <div class="abs ghost-word" style="left:0;width:1200px;text-align:center;top:1838px;font-size:95px;color:#eef0f2">REVIEWS</div>
  <h2 class="abs section-h2" style="top:1876px">TESTIMONIALS</h2>
  <svg class="abs" style="left:572px;top:1952px" width="58" height="40" viewBox="0 0 58 40"><path d="M2 14a12 12 0 1 1 22 6c-3 8-10 14-18 18l-2-3c5-3 9-7 10-12A12 12 0 0 1 2 14zM32 14a12 12 0 1 1 22 6c-3 8-10 14-18 18l-2-3c5-3 9-7 10-12A12 12 0 0 1 32 14z" fill="#5f8a0f"/></svg>
  <blockquote class="abs quote">Lorem ipsum dolor sit amet, consectetur adipiscing elit, sed do eiusmod tempor incididunt ut labore et dolore<br>magna aliqua. Ut enim ad minim veniam, quis nostrud exercitation ullamco laboris nisi ut aliquip ex ea commodo<br>consequis aute irure dolor in reprehenderit in voluptate velit esse cillum dolore</blockquote>
  <p class="abs cite"><strong>- John Doe</strong> <em>, Customer</em></p>
  <svg class="abs" style="left:176px;top:2021px" width="36" height="66" viewBox="0 0 36 66"><path d="M34 1L2 33l32 32" stroke="#999" stroke-width="1.5" fill="none"/></svg>
  <svg class="abs" style="left:988px;top:2021px" width="36" height="66" viewBox="0 0 36 66"><path d="M2 1l32 32-32 32" stroke="#999" stroke-width="1.5" fill="none"/></svg>
</section>

<section>
  <div class="abs map" role="img" aria-label="Street map of Kailua Kona showing the office location"></div>
  <address class="abs contact-card" style="font-style:normal">
    <div class="c-row" style="top:29px"><span class="c-icon" style="background:var(--navy)"><svg width="20" height="18" viewBox="0 0 20 18"><path d="M10 1L1 9h3v8h5v-5h2v5h5V9h3z" fill="#fff"/></svg></span><span>41-2280 Halewai Avenue, Suite 310<br>Kailua Kona, Hawaii 96740.</span></div>
    <div class="c-row" style="top:102px"><span class="c-icon" style="background:var(--green)"><svg width="18" height="18" viewBox="0 0 18 18"><path d="M3 1c2-1 3 0 4 3 .5 2-1 2-1 3s2.5 4 4 4.5c1 .3 1.3-1.3 2.7-.9 2.8 1 3.6 2 2.8 3.7C14.7 16 13 17 10 15.5 6 13.5 2 9 1.2 5.5.8 3 2 2 3 1z" fill="#fff"/></svg></span><span>Phone : +1.808.555.0147</span></div>
    <div class="c-row" style="top:161px"><span class="c-icon" style="background:var(--navy)"><svg width="22" height="16" viewBox="0 0 22 16"><rect x="1" y="1" width="20" height="14" rx="2" fill="none" stroke="#fff" stroke-width="2"/><path d="M2 3l9 6 9-6" stroke="#fff" stroke-width="2" fill="none"/></svg></span><span>Email : clients@tarnadvocate.example</span></div>
  </address>
</section>

<footer class="abs site-footer">
  <span class="copy">Copyright 2019 © Meridian Crest Legal Group. All Rights Reserved.</span>
  <nav><span>HOME</span><span>|</span><span>ATTORNEYS</span><span>|</span><span>PRACTICE AREAS</span><span>|</span><span>CONTACT US</span><span>|</span><span>BLOG</span></nav>
</footer>

</body>
</html>
```